Fitness Business Card Design Needed

We are looking for a business card design that stands out but is also simple and unique. I like the idea of on one side using the picture of myself with my logo at my feet. I love the texture on the business card so please take that into account when designing. Then on the other side having my contact details. I want it to be clean, modern, and pretty. I am open to designs that allow spot gloss or gold foiling.

Contact Information for Business Card

Space for Name, Phone number, email, and website

```html
<!DOCTYPE html>
<html lang="en">
<head>
<meta charset="utf-8">
<title>PetitePower Fitness – Business Card</title>
<link href="https://fonts.googleapis.com/css2?family=Montserrat:wght@400&family=Roboto:wght@400&display=swap" rel="stylesheet">
<style>
  :root {
    --backdrop: #8a8a8a;
    --card-black: #141414;
    --card-white: #f4f4f2;
    --gold: #c3943f;
    --ink: #2b2b2b;
    --ink-soft: #4a4a4a;
    --light: #e6e6e6;
  }
  html, body {
    margin: 0;
    padding: 0;
    width: 1200px;
    height: 1200px;
    overflow: hidden;
    background: var(--backdrop);
  }
  .stage {
    position: relative;
    width: 1200px;
    height: 1200px;
  }
  .card {
    position: absolute;
    top: 310px;
    height: 595px;
    box-shadow: 2px 4px 8px rgba(0,0,0,0.35);
    overflow: hidden;
  }
  .card--front {
    left: 220px;
    width: 370px;
    background:
      repeating-linear-gradient(0deg, rgba(255,255,255,0.025) 0 1px, transparent 1px 4px),
      repeating-linear-gradient(90deg, rgba(255,255,255,0.02) 0 1px, transparent 1px 4px),
      var(--card-black);
  }
  .card--back {
    left: 632px;
    width: 365px;
    background:
      repeating-linear-gradient(0deg, rgba(0,0,0,0.025) 0 1px, transparent 1px 4px),
      repeating-linear-gradient(90deg, rgba(0,0,0,0.02) 0 1px, transparent 1px 4px),
      var(--card-white);
  }
  .brand {
    position: absolute;
    left: 0;
    right: 0;
    text-align: center;
    font-family: "Montserrat", sans-serif;
    font-weight: 400;
    line-height: 1.1;
  }
  .brand__name {
    display: block;
    font-size: 25px;
    letter-spacing: 3px;
  }
  .brand__sub {
    display: block;
    font-size: 12px;
    letter-spacing: 7px;
    margin-top: 4px;
  }
  .card--front .brand { top: 60px; color: var(--light); }
  .card--back .brand { top: 222px; color: var(--ink); }
  .brand-mark {
    position: absolute;
    left: 152px;
    top: 96px;
    width: 60px;
    height: 60px;
    border: 2px solid var(--gold);
    box-sizing: border-box;
  }
  .portrait {
    position: absolute;
    left: 60px;
    top: 120px;
    width: 270px;
    height: 475px;
    background: radial-gradient(ellipse at 50% 45%, #c98e72 0%, #a8664f 40%, rgba(20,20,20,0) 75%);
  }
  .contact-person {
    position: absolute;
    top: 376px;
    left: 0;
    right: 0;
    text-align: center;
    font-family: "Roboto", sans-serif;
    font-weight: 400;
  }
  .contact-person__name {
    display: block;
    color: var(--gold);
    font-size: 24px;
    letter-spacing: 0.5px;
  }
  .contact-person__role {
    display: block;
    color: var(--ink-soft);
    font-size: 16px;
    margin-top: 2px;
  }
  .contact-icons {
    position: absolute;
    top: 442px;
    left: 86px;
  }
  .contact-list {
    position: absolute;
    top: 476px;
    left: 0;
    right: 0;
    margin: 0;
    padding: 0;
    list-style: none;
    text-align: center;
    font-family: "Roboto", sans-serif;
    font-size: 16.5px;
    line-height: 21.5px;
    color: var(--ink-soft);
  }
</style>
</head>
<body>
<main class="stage">
  <section class="card card--front">
    <div class="brand">
      <span class="brand__name">PETITEPOWER</span>
      <span class="brand__sub">FITNESS</span>
    </div>
    <div class="portrait" role="img" aria-label="Full-length photo of the trainer in a red two-piece, hands on hips"></div>
  </section>

  <section class="card card--back">
    <div class="brand-mark"></div>
    <div class="brand">
      <span class="brand__name">PETITEPOWER</span>
      <span class="brand__sub">FITNESS</span>
    </div>

    <div class="contact-person">
      <span class="contact-person__name">DANIEL HARTLEY</span>
      <span class="contact-person__role">MANAGING DIRECTOR</span>
    </div>

    <svg class="contact-icons" width="192" height="26" viewBox="0 0 192 26" aria-hidden="true">
      <line x1="0" y1="13" x2="48" y2="13" stroke="#9a9a9a" stroke-width="1"/>
      <line x1="144" y1="13" x2="192" y2="13" stroke="#9a9a9a" stroke-width="1"/>
      <circle cx="68" cy="13" r="11" fill="#c3943f"/>
      <path d="M63 9 q0 8 8 9 l2-2 -2.5-2 -1.5 1 q-2.5-1-3.5-3.5 l1-1.5 -2-2.5z" fill="#fff"/>
      <circle cx="96" cy="13" r="11" fill="#c3943f"/>
      <rect x="90" y="9" width="12" height="8" fill="#fff"/>
      <path d="M90 9 l6 5 6-5" fill="none" stroke="#c3943f" stroke-width="1"/>
      <circle cx="124" cy="13" r="11" fill="#c3943f"/>
      <circle cx="124" cy="13" r="6" fill="none" stroke="#fff" stroke-width="1.5"/>
      <path d="M118 13 h12 M124 7 q-3 6 0 12 q3-6 0-12" fill="none" stroke="#fff" stroke-width="1"/>
    </svg>

    <ul class="contact-list">
      <li>044-987 654 321</li>
      <li>HELLO@PETITEPOWER.COM</li>
      <li>WWW.PETITEPOWER.COM</li>
    </ul>
  </section>
</main>
</body>
</html>
```